Business card design for a dynamic IT consulting company

We need a business card design for a young firm, specialized in the Telecommunications/Consulting industry. The name of the company is Quindor and Partners Business Consulting Ltd. (Short name: Quindor and Partnes)
Quindor = solve read reverse, so we aim to be uncomplicated and solution-oriented. The small pipe in our logo is also related to the word solve. So we need a new business card design, which is simple, eye catching and something non traditional (I would probably prefer a square shaped design rather than a rectangle, but open for suggestions). Attached our logo.

Target Market(s)

Usually our customers are Tier1 Telecoms providers (Q-Netra, Palorix, etc) and their executives.

Industry/Entity Type

Business

Contact Information for Business Card

Name: Bence Tolnavari
Email: b.tolnavari@quindor.hu
Web: www.quindor.hu
Mobile: +36 30 518 2769
Title: Managing Director

Optional:
Company name: Quindor and Partners Ltd.
Address: 1087 Budapest, Tolvenka str. 28/C, Hungary

Font styles to use
Other font styles liked:
• helveticaneue_medium, Prime Regular are used now.

Colors

Designer to choose colors to be used in the design.

Requirements
Must have
• I would like to have a 2 sided design.
Nice to have
• I thought if we make the logo a bit bigger (without the company name), that could go to the back with the company name below. I though, if the pipe in the logo is somehow touchable on the business card, would be nice and unique.

```html
<!DOCTYPE html>
<html lang="en">
<head>
<meta charset="utf-8">
<title>Quindor and Partners – Business Card</title>
<link href="https://fonts.googleapis.com/css2?family=Work+Sans:wght@300;400;600&display=swap" rel="stylesheet">
<style>
  :root {
    --backdrop: #2b2b2b;
    --card-white: #ffffff;
    --brand-blue: #1b9ad8;
    --brand-magenta: #b52b8f;
    --brand-gray: #5f6062;
    --text-gray: #555759;
  }
  html, body {
    margin: 0;
    padding: 0;
    width: 1200px;
    height: 930px;
    overflow: hidden;
    background: var(--backdrop);
    font-family: "Work Sans", Arial, sans-serif;
  }
  .canvas { position: relative; width: 1200px; height: 930px; }
  .card {
    position: absolute;
    left: 278px;
    width: 645px;
    height: 369px;
    border-radius: 22px;
    overflow: hidden;
  }
  .card--front { top: 75px; background: var(--card-white); }
  .card--back { top: 486px; background: var(--brand-blue); }

  .wordmark {
    position: absolute;
    display: flex;
    align-items: center;
    white-space: nowrap;
    font-weight: 400;
  }
  .wordmark__square { display: inline-block; flex: none; }
  .card--front .wordmark {
    left: 43px; top: 144px;
    font-size: 27px; color: var(--brand-gray); gap: 10px;
  }
  .card--front .wordmark__square { width: 14px; height: 14px; background: var(--brand-blue); }
  .card--back .wordmark {
    left: 0; right: 0; top: 152px; justify-content: center;
    font-size: 50px; color: #fff; gap: 18px;
  }
  .card--back .wordmark__square { width: 26px; height: 26px; background: #fff; }

  .divider {
    position: absolute; left: 359px; top: 83px;
    width: 2px; height: 156px; background: var(--brand-blue);
  }
  .contact { position: absolute; left: 383px; top: 79px; color: var(--text-gray); }
  .contact__name {
    margin: 0; font-size: 23px; font-weight: 600;
    color: var(--brand-blue); letter-spacing: 0.3px; line-height: 1.2;
  }
  .contact__title { margin: 0 0 11px; font-size: 16px; font-weight: 300; line-height: 1.2; }
  .contact__address { margin: 0 0 9px; font-size: 16px; font-weight: 300; line-height: 21px; font-style: normal; }
  .contact__list { list-style: none; margin: 0; padding: 0; font-size: 16px; font-weight: 300; line-height: 20px; }
  .contact__list li { display: flex; align-items: center; gap: 10px; }
  .contact__icon { width: 12px; height: 12px; flex: none; }

  .accent-band {
    position: absolute; left: 0; right: 0; bottom: 0;
    height: 72px;
    background: linear-gradient(90deg, var(--brand-blue) 0%, var(--brand-magenta) 50%, var(--brand-gray) 100%);
  }
</style>
</head>
<body>
<main class="canvas">
  <section class="card card--front" aria-label="Business card front">
    <div class="wordmark"><span class="wordmark__square"></span>Quindor &amp; Partners</div>
    <div class="divider"></div>
    <div class="contact">
      <h1 class="contact__name">Bence Tolnavari</h1>
      <p class="contact__title">Managing Director</p>
      <address class="contact__address">1087 Budapest,<br>Tolvenka str. 28/C, Hungary</address>
      <ul class="contact__list">
        <li>
          <svg class="contact__icon" viewBox="0 0 12 12"><path d="M3 1 L5 3.5 L4 5 Q5 7 7 8 L8.5 7 L11 9 L9.5 11 Q4 10 1 3 Z" fill="none" stroke="#1b9ad8" stroke-width="1.2"/></svg>
          +36 30 518 2769
        </li>
        <li>
          <svg class="contact__icon" viewBox="0 0 12 12"><rect x="1" y="2.5" width="10" height="7" fill="none" stroke="#1b9ad8" stroke-width="1.2"/><path d="M1 2.5 L6 6.5 L11 2.5" fill="none" stroke="#1b9ad8" stroke-width="1.2"/></svg>
          b.tolnavari@quindor.hu
        </li>
        <li>
          <svg class="contact__icon" viewBox="0 0 12 12"><circle cx="6" cy="6" r="5" fill="none" stroke="#1b9ad8" stroke-width="1.1"/><ellipse cx="6" cy="6" rx="2.2" ry="5" fill="none" stroke="#1b9ad8" stroke-width="1"/><path d="M1 6 H11" stroke="#1b9ad8" stroke-width="1"/></svg>
          www.quindor.hu
        </li>
      </ul>
    </div>
    <div class="accent-band" role="img" aria-label="Decorative band in brand blue, magenta and gray along the bottom edge"></div>
  </section>

  <section class="card card--back" aria-label="Business card back">
    <div class="wordmark"><span class="wordmark__square"></span>Quindor &amp; Partners</div>
  </section>
</main>
</body>
</html>
```